Norrell Advisory WA Business Card

Create an interesting, eye catching and colourful two sided business card. We are a business consulting operation assisting SME's improve all areas of their business. We provide consulting services to assist SME's to create a culture of continuous improvement, making a positive difference in the business. Our tag line is Small changes, big rewards. We want to create a well recognised, innovative brand that can be continued throughout our website, social media and email correspondence.

Target Market(s)

Small to Medium Enterprise Business Owners

Industry/Entity Type

Business Consultant

Contact Information for Business Card

Name of Business: Norrell Advisory - Small Changes Big Rewards
Derek Holloway Ph 0407385510 Megan Holloway Ph 0407913847
Email norrelladvisorywa@mailbox-example.com
Web address TBA
FaceBook page TBA

BACKSIDE OF CARD

Providing assistance with:

• Organisation & Efficiency
• Revenue generation & Marketing
• Financial Management
• Production quality & delivery
• Systems & Process documentation
• Exit Strategy

Font styles to use
Other font styles liked:
• Calibri

Colors

Designer to choose colors to be used in the design.

Requirements
Must have
• Calibri font

```html
<!DOCTYPE html>
<html lang="en">
<head>
<meta charset="utf-8">
<title>Norrell Advisory WA Business Card</title>
<link rel="stylesheet" href="https://fonts.googleapis.com/css2?family=Carlito:wght@400;700&display=swap">
<style>
  :root {
    --backdrop: #4a4a4c;
    --card-white: #ffffff;
    --brand-red: #e8392b;
    --brand-blue: #0b7dbf;
    --heading-blue: #1479c2;
    --ink: #1d1d1d;
    --on-blue: #ffffff;
  }
  * { box-sizing: border-box; margin: 0; padding: 0; }
  html, body {
    width: 1200px; height: 1000px; overflow: hidden;
    background: var(--backdrop);
    font-family: "Carlito", "Calibri", sans-serif;
  }
  .card {
    position: absolute; left: 220px;
    width: 760px; height: 420px;
    border-radius: 26px; overflow: hidden;
    background: var(--card-white);
  }
  .card--back { top: 50px; }
  .card--front { top: 530px; display: flex; }

  .brand {
    display: flex; align-items: center; gap: 12px;
    color: var(--brand-red); font-weight: 700; letter-spacing: 0.5px;
  }
  .brand__mark { width: 22px; height: 22px; background: var(--brand-red); border-radius: 4px; }

  /* back side */
  .card--back .brand { position: absolute; top: 150px; left: 0; right: 0; justify-content: center; font-size: 40px; }
  .mission {
    position: absolute; top: 260px; left: 0; right: 0; text-align: center;
    color: var(--heading-blue); font-weight: 700; font-size: 21px; letter-spacing: 0.4px;
  }
  .services {
    position: absolute; top: 296px; left: 0; right: 0; text-align: center;
    color: var(--ink); font-size: 19px; line-height: 1.4;
  }

  /* front side */
  .front__identity {
    width: 390px; height: 100%;
    display: flex; flex-direction: column; justify-content: center; padding-left: 48px;
  }
  .front__identity .brand { font-size: 34px; }
  .tagline { margin-top: 8px; font-size: 17px; letter-spacing: 1px; color: var(--ink); }
  .front__divider { width: 10px; height: 100%; background: var(--brand-red); }
  .front__contact {
    flex: 1; background: var(--brand-blue); color: var(--on-blue);
    padding: 64px 0 0 40px;
  }
  .person { margin-bottom: 28px; }
  .person__name { font-weight: 700; font-size: 27px; letter-spacing: 0.5px; }
  .line { display: flex; align-items: center; gap: 8px; font-size: 24px; }
  .line svg { width: 18px; height: 18px; flex: none; }
  .links { margin-top: 44px; }
  .links .line { font-size: 21px; margin-bottom: 4px; }
  .links .line svg { width: 15px; height: 15px; }
</style>
</head>
<body>

<section class="card card--back" aria-label="Card back">
  <div class="brand"><span class="brand__mark"></span>NORRELL ADVISORY</div>
  <p class="mission">CREATING A CULTURE OF CONTINUOUS IMPROVEMENT</p>
  <p class="services">
    Organisation &amp; Efficiency | Revenue generation &amp; Marketing | Financial Management<br>
    Production quality &amp; delivery | Systems &amp; Process documentation | Exit Strategy
  </p>
</section>

<section class="card card--front" aria-label="Card front">
  <div class="front__identity">
    <div class="brand"><span class="brand__mark"></span>NORRELL ADVISORY</div>
    <p class="tagline">SMALL CHANGES * BIG REWARDS</p>
  </div>
  <div class="front__divider"></div>
  <div class="front__contact">
    <div class="person">
      <p class="person__name">DEREK HOLLOWAY</p>
      <p class="line">
        <svg viewBox="0 0 24 24" fill="none" stroke="currentColor" stroke-width="2"><path d="M5 3h4l2 5-3 2a12 12 0 0 0 6 6l2-3 5 2v4a2 2 0 0 1-2 2A17 17 0 0 1 3 5a2 2 0 0 1 2-2z"/></svg>
        0407385510
      </p>
    </div>
    <div class="person">
      <p class="person__name">MEGAN HOLLOWAY</p>
      <p class="line">
        <svg viewBox="0 0 24 24" fill="none" stroke="currentColor" stroke-width="2"><path d="M5 3h4l2 5-3 2a12 12 0 0 0 6 6l2-3 5 2v4a2 2 0 0 1-2 2A17 17 0 0 1 3 5a2 2 0 0 1 2-2z"/></svg>
        0407913847
      </p>
    </div>
    <div class="links">
      <p class="line">
        <svg viewBox="0 0 24 24" fill="none" stroke="currentColor" stroke-width="2"><rect x="2" y="5" width="20" height="14" rx="2"/><path d="M2 6l10 7 10-7"/></svg>
        norrelladvisorywa@mailbox-example.com
      </p>
      <p class="line">
        <svg viewBox="0 0 24 24" fill="none" stroke="currentColor" stroke-width="2"><circle cx="12" cy="12" r="10"/><path d="M2 12h20M12 2a15 15 0 0 1 0 20M12 2a15 15 0 0 0 0 20"/></svg>
        www.norrelladvisory-example.com
      </p>
      <p class="line">
        <svg viewBox="0 0 24 24"><circle cx="12" cy="12" r="9" fill="currentColor"/></svg>
        norrelladvisory
      </p>
    </div>
  </div>
</section>

</body>
</html>
```